Disposable Mini Sauce Pot Design for Asian Chain Food Brands

We operate a Hainan Chicken Rice takeout brand under the name Brindle4U, with our official website: www.Brindle4U.example.
We offer four signature house sauces and are launching brand-new packaging for our sauce line. We require custom graphic designs exclusively for the sauce cup lids.
Product Material & Base Specs
The sauce cups are made of PP plastic, available in two translucent base options: Translucent White and Translucent Orange.
Four Sauce Varieties for Individual Lid Designs
1. Red Sauce – Fried Sweet Chili Sauce
2.Green Sauce – Scallion Oil Dressing
3.Sweet Soy Sauce
4.Sweet Red Sauce (Special for Fried Chicken)
Differentiate each sauce lid design through unique graphics, typography, or illustrative elements for easy customer identification.
The marking NET WT 2 OZ must be clearly printed on every lid.
**There is no need to print full descriptive text or the full name of the sauces on each lid; the design only needs to clearly differentiate the four sauce varieties.
**Please reference the original design style and brand color palette shown on our official website, and feel free to fully unleash your creativity.
Look and feel
Each slider illustrates characteristics of the customer's brand and the style your logo design should communicate.

```html
<!DOCTYPE html>
<html lang="en">
<head>
<meta charset="utf-8">
<title>Brindle4U Sauce Lids</title>
<link rel="stylesheet" href="https://fonts.googleapis.com/css2?family=Luckiest+Guy&family=Montserrat:wght@400;700;800&display=swap">
<style>
  :root {
    --bg: #ffffff;
    --white: #ffffff;
    --red: #b40c0c;
    --red-frame: #ff2a1e;
    --red-head: #a61414;
    --amber: #f7941d;
    --green: #3f6b15;
    --green-frame: #6fa22a;
    --green-head: #3f6416;
    --brown: #3d2215;
    --brown-frame: #8c5522;
    --brown-head: #4a3122;
    --caramel: #f2b155;
    --orange: #e2470f;
    --orange-frame: #ff9000;
    --orange-head: #d9430c;
    --lime: #c9e400;
    --caption: #3a3a3a;
  }
  * { box-sizing: border-box; margin: 0; padding: 0; }
  html, body { width: 1109px; height: 1200px; overflow: hidden; background: var(--bg); }
  .sheet { position: relative; width: 1109px; height: 1200px; }
  .variant-name {
    position: absolute; width: 353px; text-align: center;
    font: 800 20px/1 "Montserrat", sans-serif; letter-spacing: .2px;
  }
  .lid {
    position: absolute; width: 353px; height: 398px; border-radius: 55px; overflow: hidden;
  }
  .lid-frame {
    position: absolute; inset: 10px; border: 2px solid; border-radius: 46px;
  }
  .brand {
    position: absolute; top: 42px; left: 0; right: 0; text-align: center;
    font: 400 27px/1 "Luckiest Guy", sans-serif; color: var(--white); letter-spacing: .5px;
  }
  .sauce-title {
    position: absolute; left: 0; right: 0; text-align: center;
    font: 400 80px/65px "Luckiest Guy", sans-serif; color: var(--white);
  }
  .sauce-title span { display: block; }
  .icon { position: absolute; left: 50%; transform: translateX(-50%); }
  .net-wt {
    position: absolute; top: 349px; left: 0; right: 0; text-align: center;
    font: 700 22px/1 "Montserrat", sans-serif; color: var(--white);
  }
  .lid-red { left: 135px; top: 150px; background: var(--red); }
  .lid-red .lid-frame { border-color: var(--red-frame); }
  .lid-green { left: 616px; top: 150px; background: var(--green); }
  .lid-green .lid-frame { border-color: var(--green-frame); }
  .lid-soy { left: 135px; top: 685px; background: var(--brown); }
  .lid-soy .lid-frame { border-color: var(--brown-frame); }
  .lid-sweet-red { left: 616px; top: 685px; background: var(--orange); }
  .lid-sweet-red .lid-frame { border-color: var(--orange-frame); }
  .accent-amber { color: var(--amber); }
  .accent-caramel { color: var(--caramel); }
  .size-note {
    position: absolute; top: 1156px; left: 0; right: 0; text-align: center;
    font: 400 18px/1 "Montserrat", sans-serif; color: var(--caption);
  }
</style>
</head>
<body>
<main class="sheet">
  <h2 class="variant-name" style="left:135px;top:94px;color:var(--red-head)">RED SAUCE</h2>
  <h2 class="variant-name" style="left:616px;top:94px;color:var(--green-head)">GREEN SAUCE</h2>
  <h2 class="variant-name" style="left:135px;top:632px;color:var(--brown-head)">SWEET SOY SAUCE</h2>
  <h2 class="variant-name" style="left:616px;top:635px;color:var(--orange-head)">SWEET RED SAUCE</h2>

  <section class="lid lid-red">
    <div class="lid-frame"></div>
    <div class="brand">Brindle4U</div>
    <h1 class="sauce-title" style="top:150px"><span>RED</span><span class="accent-amber">SAUCE</span></h1>
    <svg class="icon" style="top:306px" width="30" height="38" viewBox="0 0 30 38" aria-label="flame">
      <path d="M15 1c2 7 10 11 10 21a10 10 0 0 1-20 0c0-5 3-8 5-10 0 4 2 6 3 6-1-6 0-12 2-17z" fill="var(--amber)"/>
    </svg>
    <div class="net-wt">NET WT 2 OZ</div>
  </section>

  <section class="lid lid-green">
    <div class="lid-frame"></div>
    <div class="brand">Brindle4U</div>
    <h1 class="sauce-title" style="top:140px"><span>GREEN</span><span>SAUCE</span></h1>
    <svg class="icon" style="top:323px" width="22" height="18" viewBox="0 0 22 18" aria-label="leaf">
      <path d="M2 16C2 7 9 2 20 2c0 9-6 14-14 13z" fill="var(--white)"/>
      <path d="M3 16c4-5 8-8 13-10" stroke="var(--green)" stroke-width="1.5" fill="none"/>
    </svg>
    <div class="net-wt">NET WT 2 OZ</div>
  </section>

  <section class="lid lid-soy">
    <div class="lid-frame"></div>
    <div class="brand">Brindle4U</div>
    <h1 class="sauce-title" style="top:96px"><span>SWEET</span><span>SOY</span><span class="accent-caramel">SAUCE</span></h1>
    <svg class="icon" style="top:314px" width="18" height="26" viewBox="0 0 18 26" aria-label="drop">
      <path d="M9 1C12 8 17 13 17 18a8 8 0 0 1-16 0C1 13 6 8 9 1z" fill="var(--caramel)"/>
    </svg>
    <div class="net-wt">NET WT 2 OZ</div>
  </section>

  <section class="lid lid-sweet-red">
    <div class="lid-frame"></div>
    <div class="brand">Brindle4U</div>
    <h1 class="sauce-title" style="top:96px"><span>SWEET</span><span>RED</span><span>SAUCE</span></h1>
    <svg class="icon" style="top:316px" width="22" height="21" viewBox="0 0 22 21" aria-label="star">
      <path d="M11 1l3 6.8 7 .6-5.4 4.7 1.7 7L11 16.4 4.7 20.1l1.7-7L1 8.4l7-.6z" fill="var(--lime)"/>
    </svg>
    <div class="net-wt">NET WT 2 OZ</div>
  </section>

  <p class="size-note">SIZE : 57.50 MM (W) X 65 MM (H)__9 MM CORNER REDIOUS</p>
</main>
</body>
</html>
```